Website to design and sell sundials: www.gnomonvale.com

We have a website that creates a free paper sundial, we want to migrate from this not profit free website to a website where we will continue offering the free paper sundial model but We will also offer a manufactured sundial and sell it.
In order to understand the project, please visit:
http://www.gnomonvale.com/vertical/sundial.html and
http://www.torvel.net/landing/

The website user journey should be redesigned, including the phases that are,
select language
Show product give info
Creation/edit sundial (could be one or more phases)
View created sundial
Buy sundial.

May some of them could be combined or splitted, what It have more sense.

Requirements
Must have
• A description page user journey offering freemium paper sundial and physical sundial to sell.
• A sundial creation page for "free" paper sundial
• A result page for paper sundial
• A sell page for physical

```html
<!DOCTYPE html>
<html lang="en">
<head>
<meta charset="utf-8">
<title>GnomonVale – Sundials</title>
<link href="https://fonts.googleapis.com/css2?family=Open+Sans:wght@400;600;700;800&family=Oswald:wght@500&display=swap" rel="stylesheet">
<style>
:root{
  --red:#b8100f;
  --orange:#efa01b;
  --orange-light:#f5b640;
  --ink:#333;
  --muted:#555;
  --panel:#f1f1f1;
  --white:#fff;
  --grass-a:#3f8a25;
  --grass-b:#6aa83a;
}
*{margin:0;padding:0;box-sizing:border-box}
html,body{width:769px;height:1200px;overflow:hidden;background:var(--white)}
body{position:relative;font-family:"Open Sans",Arial,sans-serif;color:var(--ink)}
.abs{position:absolute}
/* header */
.brand{left:103px;top:22px;display:flex;align-items:center;gap:8px}
.brand-dot{width:14px;height:14px;border-radius:50%;background:var(--orange)}
.brand-name{font-size:20px;font-weight:600;color:var(--red);letter-spacing:-.3px}
.cart{left:515px;top:10px;width:58px;height:18px;background:var(--orange);color:#fff;font-size:6px;font-weight:700;display:flex;align-items:center;justify-content:center;gap:4px}
.lang{left:579px;top:9px;width:86px;height:19px;border:1px solid #ccc;font-size:6.5px;display:flex;align-items:center;padding:0 6px;justify-content:space-between}
.nav{top:36px;height:18px;font-size:6.5px;font-weight:600;display:flex;align-items:center}
.nav-home{left:382px;width:36px;background:var(--red);color:#fff;justify-content:center}
/* hero */
.hero{left:0;top:61px;width:769px;height:275px;background:radial-gradient(ellipse at 70% 45%,var(--grass-b),var(--grass-a))}
.hero-title{left:133px;top:140px;font-size:29px;font-weight:800;color:#fff;letter-spacing:.5px}
.hero-sub{left:133px;top:175px;width:280px;font-size:11px;line-height:13px;color:#fff}
.btn-buy{left:136px;top:221px;width:89px;height:23px;background:var(--orange);color:var(--red);font-size:9.5px;font-weight:800;display:flex;align-items:center;justify-content:center;gap:5px}
.dots{left:349px;top:309px;display:flex;gap:9px}
.dots span{width:5px;height:5px;border-radius:50%;background:#fff}
/* products */
.section-title{left:0;width:769px;top:350px;text-align:center;font-size:12px;font-weight:700;color:var(--red)}
.title-rule{left:339px;top:369px;width:91px;height:2px;background:var(--orange)}
.card{top:387px;width:258px;height:266px;background:#f7f7f7;border:1px solid #e6e6e6}
.card-photo{height:147px;background:linear-gradient(120deg,#6e4a37,#b9a99a 55%,#8e8a86)}
.card-title{position:absolute;left:15px;top:158px;font-size:10px;font-weight:700;color:var(--red)}
.card-text{position:absolute;left:15px;top:179px;width:232px;font-size:6.7px;line-height:10.4px;color:var(--muted)}
.price{position:absolute;left:15px;top:229px;display:flex;height:21px}
.price b{width:38px;background:var(--red);color:#fff;font-family:Oswald,sans-serif;font-weight:500;font-size:14px;display:flex;align-items:center;justify-content:center}
.price span{width:80px;background:var(--orange);color:#fff;font-size:7.5px;font-weight:700;display:flex;align-items:center;justify-content:center}
/* needs */
.needs{left:118px;top:666px;width:265px;height:184px;background:var(--orange);color:#fff}
.map{left:383px;top:666px;width:269px;height:184px;background:radial-gradient(ellipse at 60% 55%,#a38b5a,#2c4a78 60%,#1d3763)}
.block-title{position:absolute;left:24px;top:18px;font-size:11px;font-weight:700}
.block-rule{position:absolute;left:24px;top:36px;width:98px;height:1px;background:rgba(255,255,255,.5)}
.step{position:absolute;left:24px;display:flex;gap:9px;font-size:7.2px;font-weight:600;line-height:9.5px;width:210px}
.num{font-family:Oswald,sans-serif;font-weight:500;font-size:8px;flex:none}
/* instructions */
.instr{left:118px;top:862px;width:534px;height:176px;background:var(--panel)}
.instr .block-title{color:var(--red);top:14px}
.istep{position:absolute;left:25px;display:flex;gap:7px;font-size:6.8px;line-height:10px;color:var(--muted);width:290px}
.istep .num{color:var(--ink)}
.diagram{position:absolute;left:362px;top:22px;width:152px;height:138px;background:linear-gradient(135deg,#fff,#f3e6e6)}
.cta{left:118px;top:1038px;width:534px;height:42px;background:var(--red);color:#fff;font-size:10px;font-weight:800;display:flex;align-items:center;justify-content:center}
/* footer */
.footer{left:0;top:1096px;width:769px;height:104px;background:var(--orange);color:#fff}
.foot-brand{position:absolute;left:120px;top:33px;display:flex;align-items:center;gap:7px;font-size:15px;font-weight:600}
.foot-brand i{width:11px;height:11px;border-radius:50%;background:#fff}
.foot-head{position:absolute;font-size:7px;font-weight:700}
.foot-links{position:absolute;left:334px;top:40px;font-size:6.8px}
.social{position:absolute;left:575px;top:32px;display:flex;gap:3px}
.social span{width:16px;height:16px;border-radius:50%}
.foot-rule{position:absolute;left:120px;top:74px;width:528px;height:1px;background:rgba(255,255,255,.4)}
.copy{position:absolute;left:121px;top:85px;font-size:5.8px}
</style>
</head>
<body>
<header>
  <div class="abs brand"><span class="brand-dot"></span><span class="brand-name">GnomonVale.com</span></div>
  <div class="abs cart"><svg width="7" height="6" viewBox="0 0 7 6"><path d="M0 0h1.5l1 4h3.5l1-3H2" fill="none" stroke="#fff" stroke-width=".9"/></svg>MY CART</div>
  <div class="abs lang"><span>English</span><svg width="7" height="4" viewBox="0 0 7 4"><path d="M0 0l3.5 3.5L7 0" fill="none" stroke="#333"/></svg></div>
  <nav>
    <div class="abs nav nav-home">HOME</div>
    <div class="abs nav" style="left:436px">ABOUT US</div>
    <div class="abs nav" style="left:497px">SERVICES</div>
    <div class="abs nav" style="left:558px">PRODUCTS</div>
    <div class="abs nav" style="left:623px">CONTACT US</div>
  </nav>
</header>

<section class="abs hero" role="img" aria-label="Photo of a metal vertical sundial lying on green grass"></section>
<svg class="abs" style="left:48px;top:182px" width="22" height="34" viewBox="0 0 22 34"><path d="M18 2L4 17l14 15" fill="none" stroke="#fff" stroke-width="3"/></svg>
<svg class="abs" style="left:700px;top:182px" width="22" height="34" viewBox="0 0 22 34"><path d="M4 2l14 15L4 32" fill="none" stroke="#fff" stroke-width="3"/></svg>
<h1 class="abs hero-title">SUNDIALS</h1>
<p class="abs hero-sub">Sundials are instruments that tell you the time with the shadow of the sun.</p>
<div class="abs btn-buy"><svg width="10" height="8" viewBox="0 0 10 8"><path d="M0 0h2l1.4 5.5h5l1.2-4H3" fill="none" stroke="#b8100f" stroke-width="1.3"/></svg>BUY NOW</div>
<div class="abs dots"><span></span><span></span><span></span><span></span><span></span></div>

<h2 class="abs section-title">OUR PRODUCTS</h2>
<div class="abs title-rule"></div>

<article class="abs card" style="left:118px">
  <div class="card-photo" role="img" aria-label="Paper sundial fixed on a brick wall"></div>
  <h3 class="card-title">WALL SUNDIAL</h3>
  <p class="card-text">I have designed this page and integrated AtlasMaps. It helps you to easily find all the parameters needed and finally produces a printable page with a cut-out paper sundial, that can be cut and folded to give you a vertical sundial.</p>
  <div class="price"><b>99€</b><span>BUY SUNDIAL</span></div>
</article>
<article class="abs card" style="left:394px">
  <div class="card-photo" role="img" aria-label="Paper sundial fixed on a window glass"></div>
  <h3 class="card-title">WINDOW SUNDIAL</h3>
  <p class="card-text">Your sundial can be configured to show civil time or civil daylight-saving time, so that it gives you your country's official time as you can see it on TV or your watch. Furthermore it can be configured to show the natural "true local time" as you can see it on ancient sundials.</p>
  <div class="price"><b>99€</b><span>BUY SUNDIAL</span></div>
</article>

<section class="abs needs">
  <h2 class="block-title">WHAT YOU NEED</h2>
  <div class="block-rule"></div>
  <div class="step" style="top:53px"><span class="num">01.</span><span>Where is the wall where you want to put your sundial on, located it with AtlasMaps.</span></div>
  <div class="step" style="top:84px"><span class="num">02.</span><span>Select the N/S/E/W face desired, from the pull-down menu.</span></div>
  <div class="step" style="top:116px"><span class="num">03.</span><span>Select your timezone or true local time for solar time</span></div>
  <div class="step" style="top:151px"><span class="num">04.</span><span>Select if you are Daylight saving time</span></div>
</section>
<div class="abs map" role="img" aria-label="Satellite map of Europe and Africa for locating the wall"></div>

<section class="abs instr">
  <h2 class="block-title">INSTRUCTIONS</h2>
  <div class="istep" style="top:45px"><span class="num">01.</span><span>CALCULATE.</span></div>
  <div class="istep" style="top:65px"><span class="num">02.</span><span>PRINT THE PDF. To print, please select "shrink to page" in order not to deform the shape of the page.</span></div>
  <div class="istep" style="top:97px"><span class="num">03.</span><span>CUT AND FOLD: Once you have your model printed, you have to cut (RED LINES), and fold (BLUE LINES)</span></div>
  <div class="istep" style="top:128px"><span class="num">04.</span><span>PUT ON YOUR WALL. Put on your wall or Window.</span></div>
  <div class="istep" style="top:148px"><span class="num">05.</span><span>ENJOY.</span></div>
  <div class="diagram" role="img" aria-label="Cut-out template of the paper sundial with red cut lines and blue fold lines"></div>
</section>
<div class="abs cta">CLICK HERE TO BUILD YOUR CUSTOM SUNDIAL!!!</div>

<footer class="abs footer">
  <div class="foot-brand"><i></i>GnomonVale.com</div>
  <div class="foot-head" style="left:334px;top:26px">MENU</div>
  <div class="foot-links">Home &nbsp;|&nbsp; About Us &nbsp;|&nbsp; Services &nbsp;|&nbsp; Products &nbsp;|&nbsp; Contact Us</div>
  <div class="foot-head" style="left:575px;top:18px">FOLLOW US ON</div>
  <div class="social"><span style="background:#5b7fc0"></span><span style="background:#1d9bf0"></span><span style="background:#d62020"></span><span style="background:#3b5bb0"></span></div>
  <div class="foot-rule"></div>
  <div class="copy">Copyrights@ 2016 All Rights Reserved</div>
</footer>
</body>
</html>
```